IT Company requires new Business Card design.

Over the years we have had a few different business card designs. We are now due for new cards across the board for all staff. We felt this would be a good time to start fresh with a new design. Our traditional card simply had our details on the front, and a list of services on the back. We don't particularly need the list of services, we have had cards where the only thing on the rear of the card was our logo.
Feel free to be creative, we would like our tag line "Complete IT Management" to appear at some point, doesn't necessarily have to be with the logo.
I have attached samples and drafts of various previous cards we have used over the years.

```html
<!DOCTYPE html>
<html lang="en">
<head>
<meta charset="utf-8">
<title>Quellmere Networking – Complete IT Management</title>
<link rel="stylesheet" href="https://fonts.googleapis.com/css2?family=Open+Sans:ital,wght@0,300;0,600;1,400&display=swap">
<style>
  :root {
    --paper: #f0f0f0;
    --brand-blue: #0f67ab;
    --slate: #627282;
    --heading-grey: #646464;
    --service-grey: #767676;
    --url-grey: #545454;
  }
  * { margin: 0; padding: 0; box-sizing: border-box; }
  html, body { width: 1200px; height: 669px; overflow: hidden; background: var(--paper); }
  .card {
    position: relative;
    width: 1200px;
    height: 669px;
    background: var(--paper);
    font-family: "Open Sans", Arial, sans-serif;
  }
  .brand-name {
    position: absolute;
    right: 66px;
    top: 78px;
    width: 280px;
    text-align: right;
    color: var(--slate);
    font-weight: 600;
    font-size: 38px;
    line-height: 1.15;
  }
  .tagline-rule { position: absolute; left: 0; top: 246px; width: 1200px; height: 20px; }
  .tagline {
    position: absolute;
    left: 54px;
    top: 229px;
    font-size: 34px;
    font-weight: 600;
    color: var(--heading-grey);
    letter-spacing: 0.5px;
    white-space: nowrap;
  }
  .services {
    position: absolute;
    list-style: none;
    font-size: 26px;
    font-weight: 300;
    line-height: 37.8px;
    color: var(--service-grey);
    white-space: nowrap;
  }
  .services--core { left: 39px; top: 349px; }
  .services--infrastructure { left: 366px; top: 349px; }
  .services--web { left: 804px; top: 346px; }
  .website {
    position: absolute;
    right: 40px;
    top: 608px;
    font-size: 26px;
    font-style: italic;
    font-weight: 400;
    color: var(--url-grey);
    white-space: nowrap;
  }
</style>
</head>
<body>
  <main class="card">
    <div class="brand-name">Quellmere<br>Networking</div>

    <svg class="tagline-rule" viewBox="0 0 1200 20" aria-hidden="true">
      <rect x="0" y="0" width="36" height="20" fill="var(--brand-blue)"/>
      <rect x="541" y="0" width="598" height="20" fill="var(--brand-blue)"/>
      <rect x="1181" y="0" width="19" height="20" fill="var(--brand-blue)"/>
    </svg>
    <h1 class="tagline">Complete IT Management</h1>

    <ul class="services services--core">
      <li>Networking</li>
      <li>Servers</li>
      <li>Workstations</li>
      <li>Laptops</li>
      <li>Firewalls</li>
    </ul>
    <ul class="services services--infrastructure">
      <li>Data Cabling</li>
      <li>All electrical Work</li>
      <li>Server Racks</li>
      <li>Network Infrastructure</li>
      <li>Off site back up</li>
    </ul>
    <ul class="services services--web">
      <li>ADSL Connections</li>
      <li>Web Hosting</li>
      <li>Web Design</li>
      <li>Website Maintenance</li>
      <li>Domain Names PABX systems</li>
    </ul>

    <p class="website">www.quellmerenetworking.com.au</p>
  </main>
</body>
</html>
```